Silver Bloom Marisol's Cleaning Service Business Cards Project

A business card with all contact details with logo design on there (already have a logo) eye catching Logo and contact info on one side, full logo on the back, must target upper class residential and corporate companies, fitness companies, still keep it on the feminine side of things , must look elegant

Target Market(s)

Upper class homes and corporate companies

Industry/Entity Type

Cleaning Service

Contact Information for Business Card

Name: Marisol Quenby
Position: Director
ABN: 31647209853
Email: marisolssilvercleaning@tidymail.example
Number: 0417906354

Font styles to use
Decorative

Colors

Designer to choose colors to be used in the design.

Requirements
Must have
• Available Sydney Wide, contact info and logo on one side, full logo on the back
Nice to have
• Professional appearance
Should not have
• Cheap advert looking stuff

```html
<!DOCTYPE html>
<html lang="en">
<head>
<meta charset="utf-8">
<title>Silver Bloom – Business Card</title>
<link rel="stylesheet" href="https://fonts.googleapis.com/css2?family=Arvo:wght@400;700&family=Roboto:wght@400;500&family=Roboto+Condensed:wght@500&display=swap">
<style>
  :root {
    --backdrop: #c4c4c4;
    --card-dark: #2e3340;
    --aqua: #31e5dc;
    --white: #ffffff;
    --ink: #2e3340;
  }
  * { margin: 0; padding: 0; box-sizing: border-box; }
  html, body { width: 1200px; height: 960px; overflow: hidden; }
  body { background: var(--backdrop); position: relative; font-family: "Roboto", Arial, sans-serif; }

  .card { position: absolute; width: 600px; height: 342px; }
  .card--front { left: 322px; top: 108px; background: var(--card-dark); }
  .card--back { left: 320px; top: 493px; background: var(--aqua); }

  .brand { position: absolute; left: 40px; top: 0; width: 210px; height: 291px;
    display: flex; flex-direction: column; align-items: center; justify-content: center; }
  .brand__name { font-family: "Arvo", Georgia, serif; font-weight: 400; font-size: 24px;
    color: var(--aqua); letter-spacing: 0.5px; text-transform: uppercase; white-space: nowrap; }
  .brand__tagline { margin-top: 6px; font-family: "Roboto", Arial, sans-serif; font-weight: 500;
    font-size: 7.5px; letter-spacing: 2px; color: var(--white); text-transform: uppercase; white-space: nowrap; }

  .divider { position: absolute; left: 268px; top: 97px; width: 1px; height: 143px; background: rgba(255,255,255,0.35); }

  .contact { position: absolute; left: 298px; top: 108px; color: var(--white); }
  .contact__name { font-family: "Roboto Condensed", Arial, sans-serif; font-weight: 500; font-size: 21px;
    color: var(--aqua); text-transform: uppercase; line-height: 1.1; }
  .contact__role { font-family: "Roboto Condensed", Arial, sans-serif; font-weight: 500; font-size: 15px;
    color: var(--aqua); text-transform: uppercase; margin-top: 2px; }
  .contact__abn { font-size: 14.5px; margin-top: 17px; }
  .contact__line { display: flex; align-items: center; gap: 8px; font-size: 14.5px; margin-top: 9px; }
  .contact__line + .contact__line { margin-top: 4px; }
  .contact__line svg { width: 13px; height: 13px; flex: none; }

  .web-band { position: absolute; left: 0; top: 291px; width: 100%; height: 30px; background: var(--aqua);
    display: flex; align-items: center; justify-content: center;
    font-family: "Arvo", Georgia, serif; font-weight: 700; font-size: 14px; letter-spacing: 5.5px;
    color: var(--ink); text-transform: uppercase; }

  .back-brand { position: absolute; left: 0; top: 110px; width: 100%; text-align: center;
    font-family: "Arvo", Georgia, serif; font-weight: 400; font-size: 40px; color: var(--white);
    letter-spacing: 1px; text-transform: uppercase; }
  .back-web { position: absolute; left: 0; top: 288px; width: 100%; text-align: center;
    font-size: 14px; letter-spacing: 3.5px; color: var(--white); }
</style>
</head>
<body>
  <section class="card card--front">
    <div class="brand">
      <div class="brand__name">Silver Bloom</div>
      <div class="brand__tagline">Marisol's Cleaning Service</div>
    </div>
    <div class="divider"></div>
    <div class="contact">
      <div class="contact__name">Marisol Quenby</div>
      <div class="contact__role">Director</div>
      <div class="contact__abn">ABN: 31647209853</div>
      <div class="contact__line">
        <svg viewBox="0 0 24 24" aria-hidden="true"><path fill="#31e5dc" d="M6.6 10.8a15.1 15.1 0 0 0 6.6 6.6l2.2-2.2c.3-.3.7-.4 1-.2 1.1.4 2.3.6 3.6.6.6 0 1 .4 1 1V20c0 .6-.4 1-1 1A17 17 0 0 1 3 4c0-.6.4-1 1-1h3.5c.6 0 1 .4 1 1 0 1.3.2 2.5.6 3.6.1.3 0 .7-.2 1z"/></svg>
        <span>0417906354</span>
      </div>
      <div class="contact__line">
        <svg viewBox="0 0 24 24" aria-hidden="true"><path fill="#31e5dc" d="M2 5h20v14H2z"/><path fill="none" stroke="#2e3340" stroke-width="1.8" d="M2 5l10 8 10-8"/></svg>
        <span>marisolssilvercleaning@tidymail.example</span>
      </div>
    </div>
    <div class="web-band">www.silverbloom.example</div>
  </section>

  <section class="card card--back">
    <div class="back-brand">Silver Bloom</div>
    <div class="back-web">www.silverbloom.example</div>
  </section>
</body>
</html>
```